tallow-brook.com

We are a small dollar lending company that will revolutionize the industry. We will do this by being completely transparent, fee free, etc and an interest rate that normal people can afford to pay. Over 10X less than our competition. We only allow our members to pay bills " bills paid fast", within 72 hours. Payday loans typically charge from 390%-600% with a terrible payback structure. We charge 36%, period, with a payback structure over 12 months. Our site will be very simple and easy to use but elegant at the same time. We do not want the site to be too busy, less is more and easier. We will have; Home, The Story, Why tallowbrook.com, Are you eligible? Members, Clients. To become a member you have to be referred by a current client of tallowbrook.com. A lot of the busy stuff will be saved for the Members and Clients sections. The feel must be elegant, easy to use and very simple to understand. I am looking for the green, white and black combinations of colors, very similar to my logo that was designed by Fernquillo.

```html
<!DOCTYPE html>
<html lang="en">
<head>
<meta charset="utf-8">
<title>Tallow Brook — Dollar Lending</title>
<link href="https://fonts.googleapis.com/css2?family=Lato:wght@300;400;700&family=Bebas+Neue&display=swap" rel="stylesheet">
<style>
:root{
  --green:#8dc63f;
  --green-light:#a6d55c;
  --green-dark:#6aa32a;
  --black:#111;
  --nav:#2b2b2b;
  --text:#3a3a3a;
  --grey-band:#efefef;
  --grey-line:#dcdcdc;
  --social:#b8b8b8;
  --white:#fff;
}
*{margin:0;padding:0;box-sizing:border-box}
html,body{width:1120px;height:1200px;overflow:hidden;background:var(--white)}
body{position:relative;font-family:'Lato',sans-serif;color:var(--text)}
.abs{position:absolute}

.brand{left:160px;top:18px;display:flex;align-items:center;gap:10px}
.brand-dot{width:52px;height:52px;border-radius:50%;background:var(--green)}
.brand-name{font-size:28px;font-weight:400;color:var(--black);letter-spacing:-.5px}

.social{left:846px;top:26px;display:flex;gap:4px}
.social span{width:25px;height:25px;background:var(--social);display:block}
.call{right:161px;top:60px;font-size:20px;font-weight:300;color:var(--green)}
.call b{color:var(--black);font-weight:400}

.hero{left:0;top:122px;width:1120px;height:331px;background:var(--green);
  box-shadow:inset 0 -6px 8px -4px rgba(0,0,0,.15)}
.hero-photo{left:160px;top:60px;width:385px;height:271px;border-radius:50% 50% 0 0/70% 70% 0 0;
  background:radial-gradient(circle at 50% 85%,#f4efd9 0%,#d9d2b0 45%,#b9c07a 75%,#9fce55 100%)}
.hero-title{left:559px;top:66px;width:356px;border-top:1px solid rgba(255,255,255,.8);border-bottom:1px solid rgba(255,255,255,.8);
  padding:8px 0 4px;font-family:'Bebas Neue',sans-serif;font-size:38px;line-height:40px;color:var(--white);letter-spacing:-.6px;white-space:nowrap}
.perks{left:560px;top:140px;list-style:none}
.perks li{display:flex;align-items:center;gap:8px;height:32px;font-size:20px;font-weight:300;color:var(--black)}
.perks svg{width:20px;height:20px}

.nav{left:161px;top:101px;width:797px;height:42px;display:flex;background:var(--nav);border-radius:3px;overflow:hidden}
.nav a{flex:1;display:flex;align-items:center;justify-content:center;color:var(--white);font-size:12px;text-decoration:none;border-left:1px solid #444}
.nav a:first-child{border-left:0;background:var(--black)}

.clients{left:0;top:453px;width:1120px;height:112px;background:var(--grey-band);border-bottom:1px solid var(--grey-line)}
.clients h3{position:absolute;left:166px;top:19px;font-size:16px;font-weight:300;color:#333}
.client{position:absolute;top:57px;transform:translate(-50%,-50%);font-size:14px;font-weight:700;color:#555;white-space:nowrap}

.story{left:171px;top:608px;width:480px}
.story h1{font-size:38px;font-weight:300;color:var(--black);line-height:44px;margin-left:1px}
.story h1 .num{color:var(--green)}
.story h1 .strong{font-weight:400}
.lead{margin-top:14px;font-size:13px;font-weight:700;color:var(--green);line-height:19px}
.story p{font-size:12.8px;line-height:19.2px}
.gap{margin-top:19px}
.more{display:block;margin-top:8px;font-size:13px;font-weight:700;color:var(--green);text-decoration:none}

.members{left:690px;top:618px;width:263px;height:308px;border:1px solid var(--grey-line);padding:12px 14px 0 16px}
.members h2{display:flex;align-items:center;gap:8px;font-size:20px;font-weight:400;color:var(--green);padding-bottom:8px;border-bottom:1px solid var(--grey-line);margin-right:0}
.members p{margin-top:12px;font-size:12.8px;line-height:19.2px;padding-left:4px}
.members .more{margin-left:6px}

.cta{left:170px;top:974px;width:782px;height:103px;background:var(--green);border-radius:2px;overflow:hidden}
.cta-art{left:0;top:0;width:220px;height:103px;background:linear-gradient(90deg,#b4dc7c 0%,#9fd15a 60%,var(--green) 100%)}
.cta h2{position:absolute;left:216px;top:25px;font-size:43px;font-weight:300;color:var(--white);letter-spacing:.3px}
.cta-btn{position:absolute;left:618px;top:28px;width:137px;height:47px;background:var(--green-light);border:2px solid #bfe38b;border-radius:3px;
  box-shadow:0 3px 0 var(--green-dark);display:flex;align-items:center;justify-content:center;font-size:13px;font-weight:700;color:#3d5a16}

.footer{left:0;top:1128px;width:1120px;height:72px;background:#2b2b2b;text-align:center}
.footer nav{margin-top:18px;font-size:12px;color:var(--white)}
.footer nav span{color:#888;margin:0 4px}
.footer small{display:block;margin-top:6px;font-size:11px;color:#bbb}
</style>
</head>
<body>

<div class="abs brand"><span class="brand-dot"></span><span class="brand-name">TALLOW BROOK</span></div>
<div class="abs social" aria-label="Social links"><span></span><span></span><span></span><span></span></div>
<div class="abs call">CALL US <b>123.456.7890</b></div>

<section class="abs hero">
  <div class="abs hero-photo" role="img" aria-label="Fan of hundred dollar bills arranged in a circle"></div>
  <div class="abs hero-title">We Are A Dollar Lending Company</div>
  <ul class="abs perks">
    <li><svg viewBox="0 0 20 20"><path d="M2 11l5 5L18 4" fill="none" stroke="#fff" stroke-width="3"/></svg>Completely Transparent</li>
    <li><svg viewBox="0 0 20 20"><path d="M2 11l5 5L18 4" fill="none" stroke="#fff" stroke-width="3"/></svg>Fee Free Service</li>
    <li><svg viewBox="0 0 20 20"><path d="M2 11l5 5L18 4" fill="none" stroke="#fff" stroke-width="3"/></svg>Affordable Interest Rate</li>
    <li><svg viewBox="0 0 20 20"><path d="M2 11l5 5L18 4" fill="none" stroke="#fff" stroke-width="3"/></svg>Pay Bills within 72 hours and</li>
    <li><svg viewBox="0 0 20 20"><path d="M2 11l5 5L18 4" fill="none" stroke="#fff" stroke-width="3"/></svg>Much more</li>
  </ul>
</section>

<nav class="abs nav">
  <a href="#">HOME</a><a href="#">THE STORY</a><a href="#">WHY TALLOWBROOK.COM</a><a href="#">ARE YOU ELIGIBLE?</a><a href="#">MEMBERS</a><a href="#">CLIENTS</a><a href="#">CONTACT US</a>
</nav>

<section class="abs clients">
  <h3>Our Clients</h3>
  <span class="client" style="left:199px">Velora</span>
  <span class="client" style="left:323px">Marrow</span>
  <span class="client" style="left:430px">Whipton</span>
  <span class="client" style="left:546px">Wavecraft</span>
  <span class="client" style="left:676px">Corelane</span>
  <span class="client" style="left:801px">Harvest Table</span>
  <span class="client" style="left:902px">Kernelwood</span>
</section>

<section class="abs story">
  <h1><span class="num">Tallow</span> <span class="strong">Brook</span> - The Story</h1>
  <div class="lead">Lorem ipsum dolor sit amet, consectetur adipiscing elit.</div>
  <p>Sed quis nisi euismod, fermentum tellus a, lobortis quam. Vestibulum condimentum mi vitae diam tristique, egestas dignissim diam mattis. <b>Curabitur vel diam</b> in massa porttitor dictum id in lorem. Vivamus faucibus ac leo ac dignissim.</p>
  <p class="gap">Maecenas orci est, euismod facilisis feugiat sit amet, semper ut tortor. Donec eleifend accumsan nisl, nec laoreet leo iaculis sit amet. Vivamus eu <u>magna rhoncus</u>, consectetur metus ac, varius lacus. Donec ultricies, tortor quis sagittis sagittis, mauris erat ullamcorper augue, eu placerat diam nunc a lorem.</p>
  <p>Nullam eget massa vel mi posuere venenatis sed quis tortor. In hac habitasse platea dictumst. Fusce nisi tellus, fermentum a luctus eget, convallis vitae orci. In commodo egestas magna quis placerat.</p>
  <a class="more" href="#">Know More&gt;</a>
</section>

<aside class="abs members">
  <h2><svg width="28" height="20" viewBox="0 0 28 20"><circle cx="9" cy="6" r="4.5" fill="#aaa"/><circle cx="19" cy="5" r="4" fill="#aaa"/><path d="M1 19c0-6 4-8 8-8s8 2 8 8z" fill="#aaa"/><path d="M18 17c0-3-1-5-3-6 1-1 3-1 4-1 4 0 8 2 8 7z" fill="#aaa"/></svg>MEMBERS</h2>
  <p>Aenean posuere velit a erat placerat, id euismod magna rutrum. Curabitur ac sollicitudin tellus. Aenean gravida nisl ut ligula facilisis, sed sollicitudin ipsum hendrerit.</p>
  <p class="gap">Vestibulum lacinia congue commodo. Sed lorem erat, euismod at risus at, sollicitudin venenatis risus. Praesent cursus lacus ac eros feugiat, vitae eleifend felis hendrerit.</p>
  <a class="more" href="#">Know More&gt;</a>
</aside>

<section class="abs cta">
  <div class="abs cta-art" role="img" aria-label="Illustration of hands giving thumbs up with swirl ornaments"></div>
  <h2>ARE YOU ELIGIBLE?</h2>
  <div class="cta-btn">DISCOVER NOW</div>
</section>

<footer class="abs footer">
  <nav>HOME<span>/</span>THE STORY<span>/</span>WHY TALLOWBROOK.COM<span>/</span>ARE YOU ELIGIBLE?<span>/</span>MEMBERS<span>/</span>CLIENTS<span>/</span>CONTACT US</nav>
  <small>Copyright © 2014 tallow-brook.com. All rights reserved.</small>
</footer>

</body>
</html>
```